We are a new company with 2 divisions a medical research and medical product sales. We need a company logo and Business Cards. The design files need to be provided to us in Adobe Photoshop CS 5.1.

Target Market(s)

Medical Community

Industry/Entity Type

Medical

Contact Information for Business Card

Company Name - Harrowgate Lifesciences LLC
Company Address 4127 Larkspur Ave Suite 7, Gainesville Fl 32614

Requirements
Must have
• The design files need to be provided to us in Adobe Photoshop CS 5.1.

```html
<!DOCTYPE html>
<html lang="en">
<head>
<meta charset="utf-8">
<title>Harrowgate Lifesciences LLC – Business Card</title>
<link rel="stylesheet" href="https://fonts.googleapis.com/css2?family=EB+Garamond:wght@400;500&display=swap">
<style>
  :root {
    --brand-green: #15a046;
    --card-white: #ffffff;
    --card-wash: #eef1f3;
    --watermark: rgba(21, 160, 70, 0.07);
    --ink: #1c1c1c;
    --backdrop: #e6e8ea;
  }
  * { box-sizing: border-box; margin: 0; padding: 0; }
  html, body {
    width: 1200px;
    height: 900px;
    overflow: hidden;
    background: var(--backdrop);
  }
  .business-card {
    position: absolute;
    left: 180px;
    top: 195px;
    width: 840px;
    height: 510px;
    background: linear-gradient(160deg, var(--card-white) 0%, var(--card-wash) 100%);
    box-shadow: 0 10px 30px rgba(0,0,0,0.15);
    font-family: "EB Garamond", Georgia, serif;
    color: var(--ink);
    overflow: hidden;
  }
  .brand-band {
    position: relative;
    z-index: 1;
    height: 182px;
    background: var(--brand-green);
    display: flex;
    align-items: center;
    padding-left: 40px;
    gap: 22px;
  }
  .brand-dot {
    width: 70px;
    height: 70px;
    border-radius: 50%;
    background: var(--card-white);
    flex: none;
  }
  .brand-name {
    color: var(--card-white);
    font-weight: 400;
    font-size: 40px;
    line-height: 1.05;
    text-transform: uppercase;
    letter-spacing: 0.5px;
  }
  .brand-watermark {
    position: absolute;
    left: 90px;
    top: 215px;
    width: 280px;
    height: 280px;
    border-radius: 50%;
    background: var(--watermark);
  }
  .card-details {
    position: absolute;
    right: 34px;
    top: 200px;
    text-align: right;
  }
  .holder-name {
    font-size: 36px;
    font-weight: 400;
    line-height: 1.1;
  }
  .holder-title {
    font-size: 26px;
    font-weight: 500;
    line-height: 1.2;
  }
  .contact-lines {
    margin-top: 30px;
    font-size: 24px;
    line-height: 1.2;
  }
</style>
</head>
<body>
  <div class="business-card">
    <div class="brand-band">
      <span class="brand-dot"></span>
      <div class="brand-name">Harrowgate<br>Lifesciences LLC.</div>
    </div>
    <span class="brand-watermark" aria-hidden="true"></span>
    <div class="card-details">
      <p class="holder-name">John Doe</p>
      <p class="holder-title">Chief Executive Officer</p>
      <div class="contact-lines">
        <p>4127 Larkspur Ave Suite 7</p>
        <p>Gainesville Fl 32614</p>
        <p>Tel: 123 456 789</p>
        <p>Email: yourname@yourcompany.com</p>
        <p>www.yourcompany.com</p>
      </div>
    </div>
  </div>
</body>
</html>
```